Larkspur Talent IT Recruiting firm needs a business card design for Recruiters, Sourcers, and Account

We need business cards that allow us to change all contact info, names, titles (Recruiter, Sourcer, Account Manager, Director, CEO, etc) per person since we have three offices, in three cities, Phoenix, Austin, and Las Vegas. We do recruiting and contractors for IT positions (Developers, Architects, Software Engineers, Security Engineers, Help Desk, DBAs, PMs, Scrum Masters, etc.) Our client companies are very diverse from Meridian 100 to silicone Valley type start-ups.

So, while we what hip, techie, and quirky, it still needs to be professional. Primary color we use is blue, with silver as a secondary color.

Target Market(s)

IT, Technology

Industry/Entity Type

Business

Contact Information for Business Card

Company name: Larkspur Talent, Inc.
Website: www.larkspurtalent.example
Logos for Careerloop, Blipster, and Myriada

Name, Title, Office Number, Cell Number, email

Font styles to use
Serif
Sans Serif

Colors
0455a3
d5d5d5

Requirements
Nice to have
• The grey I selected below is not necessary - but, would like silver included. I included a card design (File 3: LTI early trial example.jpg) that I had started on. It's very rough, and not quite what we're looking for, but what we did like is the logo, big, maybe a bit faded, off center, goes out of frame, etc. Still looking for other ideas - you are the pros! But, just an idea of a design element we liked.

```html
<!DOCTYPE html>
<html lang="en">
<head>
<meta charset="utf-8">
<title>Larkspur Talent — Business Card</title>
<link rel="stylesheet" href="https://fonts.googleapis.com/css2?family=Cinzel:wght@400;600&family=Open+Sans:wght@400;700&display=swap">
<style>
  :root {
    --stage: #3b3b3d;
    --card-dark: #111214;
    --card-dark-edge: #26272a;
    --card-light: #ffffff;
    --brand-blue: #1d8fe0;
    --brand-deep: #0455a3;
    --silver: #d5d5d5;
    --ink: #1e1e1e;
    --ink-soft: #4a4a4a;
  }
  * { box-sizing: border-box; margin: 0; padding: 0; }
  html, body { width: 1200px; height: 852px; overflow: hidden; }
  body {
    background: var(--stage);
    position: relative;
    font-family: "Open Sans", Arial, sans-serif;
  }
  .card {
    position: absolute;
    width: 560px;
    height: 320px;
    border-radius: 18px;
    overflow: hidden;
    box-shadow: 0 14px 30px rgba(0,0,0,.45);
  }

  /* Front */
  .card-front {
    left: 150px; top: 80px;
    background: linear-gradient(135deg, var(--card-dark-edge) 0%, var(--card-dark) 55%, #0b0b0c 100%);
  }
  .front-decoration {
    position: absolute;
    right: -90px; top: -120px;
    width: 420px; height: 420px;
    border-radius: 50%;
    background: radial-gradient(circle, rgba(255,255,255,.06) 0%, rgba(255,255,255,.02) 60%, rgba(255,255,255,0) 72%);
  }
  .front-lockup {
    position: absolute;
    left: 0; right: 0; top: 108px;
    text-align: center;
  }
  .wordmark {
    font-family: "Cinzel", "Times New Roman", serif;
    font-weight: 400;
    letter-spacing: 2px;
    display: inline-flex;
    align-items: center;
    gap: 12px;
    white-space: nowrap;
  }
  .wordmark-dot {
    border-radius: 50%;
    background: var(--brand-blue);
    flex: none;
  }
  .card-front .wordmark { font-size: 40px; color: #ffffff; }
  .card-front .wordmark-dot { width: 30px; height: 30px; }
  .tagline {
    font-family: "Cinzel", "Times New Roman", serif;
    letter-spacing: 2px;
    white-space: nowrap;
  }
  .card-front .tagline {
    margin-top: 44px;
    font-size: 17px;
    color: #f2f2f2;
  }

  /* Back */
  .card-back {
    left: 480px; top: 440px;
    background: linear-gradient(160deg, #ffffff 0%, #f6f6f6 100%);
  }
  .back-band {
    position: absolute; left: 0; bottom: 0;
    width: 100%; height: 60px;
  }
  .back-identity {
    position: absolute; left: 24px; top: 62px; width: 304px;
  }
  .card-back .wordmark { font-size: 23px; color: var(--ink); gap: 8px; letter-spacing: 1px; }
  .card-back .wordmark-dot { width: 18px; height: 18px; }
  .card-back .tagline {
    margin-top: 16px; font-size: 12.5px; color: var(--ink); text-align: center;
  }
  .person {
    margin-top: 24px; text-align: right; padding-right: 10px;
  }
  .person-name {
    font-weight: 700; font-size: 15px; color: var(--brand-blue); letter-spacing: .3px;
  }
  .person-title { font-size: 10px; color: var(--ink-soft); margin-top: 1px; }
  .social-list {
    list-style: none; margin-top: 10px;
    display: flex; justify-content: flex-end; gap: 8px;
  }
  .social-list li {
    font-size: 9px; font-weight: 700; color: var(--brand-blue);
  }
  .divider {
    position: absolute; left: 338px; top: 50px;
    width: 1px; height: 150px; background: var(--silver);
  }
  .contact {
    position: absolute; left: 356px; top: 60px;
    font-size: 10.5px; color: var(--ink); line-height: 1.45;
  }
  .contact-address { margin-bottom: 10px; }
  .contact-list { list-style: none; }
  .contact-list li { display: flex; align-items: center; gap: 8px; }
  .contact-list svg { width: 11px; height: 11px; fill: var(--brand-deep); flex: none; }
</style>
</head>
<body>

  <section class="card card-front">
    <div class="front-decoration" role="img" aria-label="Large faded brand emblem bleeding off the card edge"></div>
    <div class="front-lockup">
      <div class="wordmark"><span class="wordmark-dot"></span>LARKSPUR TALENT</div>
      <p class="tagline">GROWING TALENT FORWARD</p>
    </div>
  </section>

  <section class="card card-back">
    <svg class="back-band" viewBox="0 0 560 60" preserveAspectRatio="none" aria-hidden="true">
      <polygon points="0,38 560,6 560,60 0,60" fill="#1d8fe0"/>
      <polygon points="0,50 560,18 560,60 0,60" fill="#0455a3" opacity=".35"/>
      <polygon points="0,34 560,2 560,6 0,38" fill="#d5d5d5"/>
    </svg>

    <div class="back-identity">
      <div class="wordmark"><span class="wordmark-dot"></span>LARKSPUR TALENT</div>
      <p class="tagline">GROWING TALENT FORWARD</p>
      <div class="person">
        <p class="person-name">DORIAN VALE</p>
        <p class="person-title">CEO</p>
        <ul class="social-list">
          <li>Blipster</li>
          <li>Careerloop</li>
          <li>Myriada</li>
        </ul>
      </div>
    </div>

    <div class="divider"></div>

    <div class="contact">
      <p class="contact-address">4210 E Quillan Ave, Suite 300<br>Brightwater, AZ 85999, USA</p>
      <ul class="contact-list">
        <li><svg viewBox="0 0 12 12" aria-hidden="true"><path d="M2.5 1l2 2-1 1.5c.6 1.4 1.6 2.4 3 3L8 6.5l2 2-1.2 2C5 10 2 7 1.5 2.2z"/></svg>555| 014-2210</li>
        <li><svg viewBox="0 0 12 12" aria-hidden="true"><rect x="3" y="1" width="6" height="10" rx="1.2"/></svg>555| 018-4477</li>
        <li><svg viewBox="0 0 12 12" aria-hidden="true"><path d="M1 3h10v6H1z M1 3l5 3.5L11 3" stroke="#fff" stroke-width=".8"/></svg>dorian@larkspurtalent.example</li>
        <li><svg viewBox="0 0 12 12" aria-hidden="true"><circle cx="6" cy="6" r="5"/></svg>www.larkspurtalent.example</li>
      </ul>
    </div>
  </section>

</body>
</html>
```